Luxury Business Card Design for High-End Window Treatments

Gilded Slatworks
Custom Plantation Shutters & Architectural Shading Systems

⸻

BACK

Daniel Trevick
Owner

Custom Interior & Exterior Window Treatments

919-555-0148
gildedslatworks.com

I have included a picture that I’m hoping we can use on the back, but I’m also wondering if you can get rid of the ladder? Should we get rid of shutters , shades and blinds underneath Gilded Slatworks?

Target Market(s)

High-end residential homeowners, custom home builders, architects, interior designers, and luxury renovation clients seeking premium plantation shutters and motorized architectural shading systems.

Industry/Entity Type

Custom Window treatments

Contact Information for Business Card

Front Gilded Slatworks Custom Plantation Shutters Motorized Architectural Shading Systems BACK Daniel Trevick Owner 919-555-0148 GildedSlatworks.com Custom Interior & Exterior Window Treatments By Appointment

Requirements
Nice to have
• Not 100% sure on nice to halves or the color but you can definitely check out my website to get a better understanding of what I’m trying to do

```html
<!DOCTYPE html>
<html lang="en">
<head>
<meta charset="utf-8">
<title>Gilded Slatworks – Business Card</title>
<link rel="stylesheet" href="https://fonts.googleapis.com/css2?family=Open+Sans:wght@400;600&family=Montserrat:wght@700&family=Alegreya+Sans+SC:wght@700&display=swap">
<style>
  :root {
    --backdrop: #e9e9e8;
    --card-black: #191919;
    --gold: #e8c34a;
    --gold-edge: #c9a233;
    --cream: #f1ece0;
    --soft-white: #e6e6e6;
    --sky: #7fa6cf;
    --siding: #cfc6b2;
    --brick: #5b4a40;
    --lawn: #5d6b3a;
  }
  * { box-sizing: border-box; margin: 0; padding: 0; }
  html, body { width: 1200px; height: 801px; overflow: hidden; }
  body {
    background: var(--backdrop);
    font-family: "Open Sans", Arial, sans-serif;
    position: relative;
  }
  .card {
    position: absolute;
    top: 230px;
    width: 560px;
    height: 320px;
    background: var(--card-black);
    border-bottom: 4px solid var(--gold-edge);
    overflow: hidden;
  }
  .card--front { left: 30px; }
  .card--back { left: 610px; }

  /* Front */
  .brand {
    position: absolute;
    left: 60px;
    top: 44px;
    width: 300px;
    text-align: center;
  }
  .brand__name {
    font-family: "Open Sans", Arial, sans-serif;
    font-weight: 400;
    font-size: 40px;
    line-height: 1.05;
    color: var(--cream);
  }
  .brand__services {
    margin-top: 10px;
    display: flex;
    justify-content: center;
    gap: 22px;
    font-family: "Alegreya Sans SC", Georgia, serif;
    font-weight: 700;
    font-size: 19px;
    color: var(--gold);
  }
  .person {
    position: absolute;
    left: 60px;
    top: 176px;
    width: 300px;
    text-align: center;
  }
  .person__name {
    font-family: "Montserrat", Arial, sans-serif;
    font-weight: 700;
    font-size: 22px;
    letter-spacing: 0.5px;
    color: var(--gold);
    text-transform: uppercase;
  }
  .person__role {
    font-size: 15px;
    color: var(--soft-white);
    margin-top: 2px;
  }
  .divider {
    position: absolute;
    left: 36px;
    right: 36px;
    top: 240px;
    height: 1px;
    background: var(--gold);
  }
  .contact {
    position: absolute;
    left: 40px;
    top: 254px;
    list-style: none;
    font-size: 16px;
    line-height: 1.35;
    color: var(--soft-white);
  }
  .contact li { display: flex; align-items: center; gap: 6px; }
  .contact svg { width: 12px; height: 12px; fill: var(--gold); }
  .tagline {
    position: absolute;
    right: 40px;
    top: 254px;
    text-align: right;
    font-size: 15px;
    line-height: 1.3;
    color: var(--soft-white);
  }

  /* Back */
  .storefront {
    position: absolute;
    inset: 0;
  }
  .storefront svg { width: 100%; height: 100%; display: block; }
  .statement {
    position: absolute;
    left: 230px;
    top: 196px;
    width: 316px;
    padding: 6px 10px;
    background: rgba(20, 20, 20, 0.45);
    font-size: 14.5px;
    line-height: 1.3;
    color: #ffffff;
  }
</style>
</head>
<body>

<section class="card card--front" aria-label="Business card front">
  <div class="brand">
    <div class="brand__name">Gilded<br>Slatworks</div>
    <div class="brand__services"><span>Shutters</span><span>Shades</span><span>Blinds</span></div>
  </div>
  <div class="person">
    <div class="person__name">Daniel Trevick</div>
    <div class="person__role">Owner</div>
  </div>
  <div class="divider"></div>
  <ul class="contact">
    <li>
      <svg viewBox="0 0 24 24" aria-hidden="true"><path d="M6.6 10.8c1.4 2.8 3.8 5.1 6.6 6.6l2.2-2.2c.3-.3.7-.4 1-.2 1.1.4 2.3.6 3.6.6.6 0 1 .4 1 1V20c0 .6-.4 1-1 1C10.6 21 3 13.4 3 4c0-.6.4-1 1-1h3.5c.6 0 1 .4 1 1 0 1.3.2 2.5.6 3.6.1.3 0 .7-.2 1l-2.3 2.2z"/></svg>
      919-555-0148
    </li>
    <li>
      <svg viewBox="0 0 24 24" aria-hidden="true"><circle cx="12" cy="12" r="10"/></svg>
      gildedslatworks.com
    </li>
  </ul>
  <p class="tagline">Custom Interior &amp; Exterior<br>Window Treatments</p>
</section>

<section class="card card--back" aria-label="Business card back">
  <div class="storefront">
    <svg viewBox="0 0 560 320" preserveAspectRatio="none" role="img" aria-label="Photo of the showroom porch with shutters, a storefront sign, shrubs and two white lawn chairs">
      <defs>
        <linearGradient id="photo-tones" x1="0" y1="0" x2="0" y2="1">
          <stop offset="0" stop-color="var(--sky)"/>
          <stop offset="0.3" stop-color="var(--siding)"/>
          <stop offset="0.6" stop-color="var(--brick)"/>
          <stop offset="1" stop-color="var(--lawn)"/>
        </linearGradient>
      </defs>
      <path d="M560 0 V316 H180 C200 240 220 150 250 80 C270 35 300 10 330 0 Z" fill="url(#photo-tones)"/>
    </svg>
  </div>
  <p class="statement">Custom Plantation Shutters &amp;<br>Motorized Architectural Shading Systems</p>
</section>

</body>
</html>
```